Logo + Label Design (Men’s Grooming Brand & Product Packaging)

Design a logo and 2 oz pomade label for Brel, a modern men’s grooming brand focused on clean, high-quality, natural ingredients. The design should establish a bold, masculine, minimalist identity that can later extend to products like shaving gel and body wash.

Key Requirements

Create a primary logo for “Brel” and a core label for the 2 oz pomade jar (screw-top).

Use a clean, modern style — masculine, confident, and approachable (think Dorran’s, Velta, Northfield Kit).

Design for 1–2 color screen printing on solid jar colors (white, black, or navy).

Avoid gradients, foil, or embossing. Must work in black & white.

Provide: vector logo, mockup of the 2 oz jar, color palette (CMYK/RGB/HEX), and font specs.

Winning design may lead to future projects (body wash, shave gel, skincare lines).

Font styles to use
Other font styles liked:
• We like the fonts and design concept in the attached mockup.

Requirements
Should not have
• We want to avoid too much writing or busy designs. We want to avoid having graphics/illustrations embedded in the logo if they will cause the brand to look less classy or sophisticated. We also want the design to look simple and all-American (e.g. Hollister and Vane, Pine Ledger, The KIM, etc). We’d like to give a Pellham & Royce vibe that feels classy and high end.

```html
<!DOCTYPE html>
<html lang="en">
<head>
<meta charset="utf-8">
<title>Brel Men's Hair Pomade – Label Artwork</title>
<link rel="stylesheet" href="https://fonts.googleapis.com/css2?family=Jost:wght@400;500;600;700&family=Arimo:wght@400&display=swap">
<style>
  :root {
    --ink: #000000;
    --paper: #ffffff;
    --backdrop: #acac9f;
  }
  * { margin: 0; padding: 0; box-sizing: border-box; }
  html, body {
    width: 1200px; height: 1200px; overflow: hidden;
    background: var(--backdrop);
    font-family: "Jost", sans-serif;
    color: var(--ink);
  }
  .artboard {
    position: relative;
    width: 1200px; height: 1200px;
  }

  /* Wrap-around band label */
  .band-label {
    position: absolute;
    left: 26px; top: 300px;
    width: 1148px; height: 138px;
    background: var(--paper);
    display: flex;
    align-items: center;
    padding: 0 12px;
  }
  .directions {
    width: 430px;
    font-size: 12.4px;
    line-height: 1.25;
    text-transform: uppercase;
    text-align: justify;
    letter-spacing: 0.02em;
  }
  .directions-title { display: block; text-align: left; }
  .wordmark {
    font-family: "Jost", sans-serif;
    font-weight: 700;
    letter-spacing: -0.04em;
    line-height: 1;
  }
  .band-label .wordmark {
    font-size: 118px;
    margin-left: 24px;
    width: 216px;
  }
  .product-block {
    margin-left: 14px;
    width: 210px;
    display: flex; flex-direction: column; align-items: flex-start;
  }
  .product-type {
    font-size: 17.5px; font-weight: 400; letter-spacing: 0.06em; line-height: 1.1;
  }
  .product-scent {
    font-size: 24.5px; font-weight: 400; letter-spacing: 0.07em; line-height: 1.2;
  }
  .product-spec {
    font-size: 10.6px; font-weight: 600; letter-spacing: 0.1em; margin-top: 3px;
  }
  .net-weight {
    background: var(--ink); color: var(--paper);
    font-family: "Arimo", sans-serif;
    font-size: 10.5px; padding: 1px 6px; margin-top: 7px;
  }
  .info-block {
    margin-left: 20px;
    font-family: "Arimo", sans-serif;
    font-size: 8.4px;
    line-height: 1.35;
    text-transform: uppercase;
  }
  .benefits { list-style: none; margin-bottom: 9px; }
  .benefits li::before { content: "• "; }
  .maker { font-size: 9.2px; }

  /* Round lid label */
  .lid-label {
    position: absolute;
    left: 425px; top: 560px;
    width: 350px; height: 350px;
  }
  .lid-label svg { display: block; }
  .lid-ring-text {
    font-family: "Jost", sans-serif; font-size: 12px; letter-spacing: 0.02em;
  }
  .lid-center {
    position: absolute; inset: 0;
    display: flex; flex-direction: column; align-items: center;
    padding-top: 62px;
  }
  .lid-center .wordmark { font-size: 66px; }
  .lid-center .product-type { font-size: 19px; margin-top: 12px; }
  .lid-center .product-scent { font-size: 19px; letter-spacing: 0.08em; margin-top: 4px; }
  .lid-center .product-spec { font-size: 11px; margin-top: 10px; }
  .lid-center .net-weight { font-size: 11px; margin-top: 10px; }
</style>
</head>
<body>
<main class="artboard">

  <section class="band-label" aria-label="Jar wrap label">
    <p class="directions">
      <span class="directions-title">Directions:</span>
      Melt small amount of pomade between hands before massaging into damp hair (for sleeker look) or dry hair (for more texture). Style as desired. For external use only. Avoid contact with eyes. If irritation occurs, discontinue use.
    </p>
    <div class="wordmark">Brel</div>
    <div class="product-block">
      <span class="product-type">MEN’S HAIR POMADE</span>
      <span class="product-scent">FRESH &amp; CLEAN</span>
      <span class="product-spec">MEDIUM HOLD ● MATTE FINISH</span>
      <span class="net-weight">NET WT 2 OZ (57 G)</span>
    </div>
    <div class="info-block">
      <ul class="benefits">
        <li>Naturally derived plant &amp; bee-based ingredients</li>
        <li>Alcohol free, non-irritating</li>
        <li>Formulated to minimize scalp irritation</li>
      </ul>
      <p class="maker">Manufactured by:<br>Brel Health Products, Ashford, NC 27514<br>Visit us at brelhealthproducts.com</p>
    </div>
  </section>

  <section class="lid-label" aria-label="Jar lid label">
    <svg width="350" height="350" viewBox="0 0 350 350">
      <defs>
        <path id="ring-path" d="M 31 175 A 144 144 0 1 1 319 175 A 144 144 0 1 1 31 175"/>
      </defs>
      <circle cx="175" cy="175" r="175" fill="var(--paper)"/>
      <circle cx="175" cy="175" r="164" fill="none" stroke="var(--ink)" stroke-width="9"/>
      <circle cx="175" cy="175" r="134" fill="none" stroke="var(--ink)" stroke-width="1.6"/>
      <text class="lid-ring-text" fill="var(--ink)">
        <textPath href="#ring-path" startOffset="24%" text-anchor="middle">Alcohol Free, Non-Irritating</textPath>
      </text>
      <text class="lid-ring-text" fill="var(--ink)">
        <textPath href="#ring-path" startOffset="32%">Formulated to minimize scalp irritation</textPath>
      </text>
      <text class="lid-ring-text" fill="var(--ink)">
        <textPath href="#ring-path" startOffset="61%">Naturally derived plant &amp; bee-based ingredients</textPath>
      </text>
    </svg>
    <div class="lid-center">
      <div class="wordmark">Brel</div>
      <span class="product-type">MEN’S HAIR POMADE</span>
      <span class="product-scent">FRESH &amp; CLEAN</span>
      <span class="product-spec">MEDIUM HOLD ● MATTE FINISH</span>
      <span class="net-weight">NET WT 2 OZ (57 G)</span>
    </div>
  </section>

</main>
</body>
</html>
```